Web Site Design for a Finance (lending) Company

We are opening a new subsidiary that focuses on lending money in the real estate industry. We need a web site designed to represent the business.

The business is lending money to real estate investors. A typical client/borrower will be looking to borrow money to buy a house, renovate it and then sell it at a profit, all within 12 months or less.

Company name is RTV Finance. Our logo is attached.

Attached is a general outline for the web site. We're working on writing more text for each page but this should give you enough to get started with some ideas.

Competitor web site that I like a lot (as an example): https://dorvaleqcapital.example/. Many of the general items on this site match what we will need (description of loan programs, FAQ)

Target Market(s)

Real estate investors (generally individuals or small companies with just a few people) who are buying homes, renovating them and then selling them at a profit.

Industry/Entity Type

Finance

Coding

Coded - Design and coding required

Number of Pages Required

5+ page

Colors

Designer to choose colors to be used in the design.

Requirements
Must have
• Minimalist design. Clean lines without too much clutter. Some stock photography is ok but the photos should not be distracting. They should almost fade in to the background so that user can focus on the key information about what our company does instead. We are a finance company, not a design company, so the information about our products will be more interesting to site visitors than the art.
• Some minimalist examples from Snapboard:
• https://www.snapboardia.example/explore/minimalist-web-design/
Nice to have
• If you search in zoovle for "hard money lenders" you will find many examples of web sites from our competition. I have provided a link above to competitor web site that I like a lot.
• I have attached our logo in EPS format. Logo is green. Web site doesn't have to be green but it should be of a color that will work well with the logo.

```html
<!DOCTYPE html>
<html lang="en">
<head>
<meta charset="utf-8">
<title>RTV Finance – Real Estate Lending</title>
<link rel="stylesheet" href="https://fonts.googleapis.com/css2?family=Lato:wght@400;700&family=Open+Sans:wght@400;600;700&display=swap">
<style>
:root{
  --green:#024d2c;
  --green-dark:#013a21;
  --charcoal:#333333;
  --charcoal-2:#3a3a3a;
  --black:#151515;
  --footer:#2f2f2f;
  --text:#444444;
  --muted:#8a8a8a;
  --white:#ffffff;
  --line:#dddddd;
}
*{box-sizing:border-box;margin:0;padding:0}
html,body{width:1200px;height:3279px;overflow:hidden}
body{position:relative;background:var(--white);font-family:"Lato",sans-serif;color:var(--text)}
.abs{position:absolute}
.heading{font-family:"Open Sans",sans-serif}

/* header */
.brand{left:0;width:1200px;top:30px;text-align:center;display:flex;justify-content:center;align-items:center;gap:12px}
.brand-mark{width:26px;height:26px;background:var(--green)}
.brand-name{font-family:"Open Sans",sans-serif;font-weight:700;font-size:30px;color:var(--green)}
.main-nav{left:79px;top:116px;width:1042px;height:50px;background:var(--green);display:flex;justify-content:center;align-items:center;gap:58px;z-index:3;box-shadow:0 3px 6px rgba(0,0,0,.3)}
.main-nav a{color:var(--white);text-decoration:none;font-size:16px;font-family:"Open Sans",sans-serif}

/* hero */
.hero-photo{left:0;top:125px;width:1200px;height:531px;background:linear-gradient(120deg,#3b4b55 0%,#9fb4bb 35%,#d8e3e4 60%,#b9ccd0 100%)}
.slider-arrow{top:358px;width:46px;height:34px;background:rgba(120,120,120,.7);display:flex;align-items:center;justify-content:center}
.chat-box{left:811px;top:531px;width:310px;height:125px;background:rgba(60,60,60,.85);color:var(--white);font-size:18px;line-height:29px;text-align:center;padding:22px 20px}
.chat-tab{left:811px;top:656px;width:310px;height:82px;z-index:2}
.chat-tab span{position:absolute;left:0;width:310px;top:18px;text-align:center;color:var(--white);font-family:"Open Sans",sans-serif;font-weight:600;font-size:22px}
.hero-band{left:0;top:656px;width:1200px;height:240px;background:var(--charcoal)}
.hero-title{left:86px;top:688px;color:var(--white);font-size:40px;line-height:52px;font-weight:600}
.btn{display:flex;align-items:center;justify-content:center;font-family:"Open Sans",sans-serif;font-size:20px;color:var(--white);text-decoration:none;border:2px solid var(--white)}
.btn-green{background:var(--green);border-color:#cfd9d3}

/* about */
.section-title{left:0;width:1200px;text-align:center;font-family:"Open Sans",sans-serif;font-size:44px;letter-spacing:-1px}
.section-title .light{color:#666;font-weight:400}
.section-title .strong{color:var(--green);font-weight:700}
.about-intro{left:150px;width:900px;top:985px;text-align:center;font-size:15px;line-height:26px;color:#666}
.feature{top:1050px;width:330px}
.feature-head{display:flex;align-items:center;gap:18px}
.feature-icon{width:72px;height:72px;border-radius:50%;background:var(--green);display:flex;align-items:center;justify-content:center;flex:none}
.feature-name{font-family:"Open Sans",sans-serif;font-size:23px;color:#333;line-height:28px}
.feature-text{margin-top:16px;font-size:15px;line-height:26px;color:#444}
.read-more{display:inline-block;margin-top:4px;font-size:14px;color:#333;text-decoration:underline}

/* fix and flip */
.flip{left:0;top:1257px;width:1200px;height:420px}
.flip-photo{left:500px;top:0;width:700px;height:420px;background:linear-gradient(160deg,#d9c9a6 0%,#a99366 40%,#5f7a3b 75%,#3f5c27 100%)}
.flip-title{left:79px;top:1348px;font-size:35px;color:var(--white);font-weight:600}
.flip-text{left:79px;top:1398px;width:440px;font-size:15px;line-height:26px;color:var(--white)}

/* cta band */
.cta{left:0;top:1677px;width:1200px;height:155px}
.cta-text{left:81px;top:1708px;font-family:"Open Sans",sans-serif;font-size:31px;line-height:42px;color:#777}
.cta-text b{color:var(--white);font-weight:600}
.cta-link{left:824px;top:1733px;font-family:"Open Sans",sans-serif;font-size:30px;color:var(--white);font-weight:600}
.cta-link::after{content:"";display:block;width:68px;height:2px;background:#ccc;margin:14px 0 0 8px}

/* commercial */
.commercial{left:0;top:1832px;width:1200px;height:415px}
.commercial-photo{left:0;top:0;width:700px;height:415px;background:linear-gradient(200deg,#cfe0ef 0%,#7d9db8 40%,#4f6a82 70%,#2c3d4d 100%)}
.commercial-title{right:79px;top:1932px;font-size:35px;color:var(--white);font-weight:600;text-align:right}
.commercial-text{right:79px;top:1985px;width:520px;font-size:15px;line-height:26px;color:var(--white);text-align:right}

/* team */
.member{width:498px;height:228px}
.member-card{position:absolute;left:52px;top:0;width:446px;height:228px;background:var(--white);box-shadow:0 2px 8px rgba(0,0,0,.25)}
.member-photo{position:absolute;left:0;top:14px;width:200px;height:200px;border:3px solid var(--green);background:linear-gradient(160deg,#e8e4df 0%,#c9c2ba 55%,#3a4450 100%)}
.member-name{position:absolute;left:222px;top:42px;font-family:"Open Sans",sans-serif;font-size:22px;color:var(--green)}
.member-bio{position:absolute;left:222px;top:80px;width:250px;font-size:15px;line-height:25px;color:#444}

/* footer */
.footer{left:0;top:2914px;width:1200px;height:312px;background:var(--footer)}
.footer-title{top:2946px;font-family:"Open Sans",sans-serif;font-size:29px;color:var(--white);letter-spacing:1px}
.footer-divider{left:601px;top:2946px;width:2px;height:236px;background:var(--green)}
.quote{left:99px;width:440px;display:flex;align-items:center;gap:22px}
.avatar{width:84px;height:84px;border-radius:50%;border:3px solid var(--white);background:linear-gradient(160deg,#f1e6dc,#b49a86);flex:none}
.quote p{font-size:14px;line-height:22px;color:var(--white)}
.contact-row{left:630px;display:flex;align-items:center;gap:20px;color:var(--white);font-size:14px;line-height:24px}
.bottom-bar{left:0;top:3226px;width:1200px;height:53px;background:var(--green);color:var(--white);font-size:15px;display:flex;align-items:center;justify-content:center}
</style>
</head>
<body>

<header>
  <div class="abs brand"><span class="brand-mark"></span><span class="brand-name">RTV Finance</span></div>
  <nav class="abs main-nav">
    <a href="#">HOME</a><a href="#">ABOUT US</a><a href="#">LOANS</a><a href="#">RESOURCES</a><a href="#">CONTACT US</a>
  </nav>
</header>

<section class="hero">
  <div class="abs hero-photo" role="img" aria-label="Photo of a model house on a desk with a pen, papers and a handshake in the background"></div>
  <div class="abs slider-arrow" style="left:0"><svg width="20" height="14"><path d="M18 7H3M8 2L3 7l5 5" stroke="#fff" stroke-width="2" fill="none"/></svg></div>
  <div class="abs slider-arrow" style="left:1154px"><svg width="20" height="14"><path d="M2 7h15M12 2l5 5-5 5" stroke="#fff" stroke-width="2" fill="none"/></svg></div>
  <div class="abs hero-band"></div>
  <div class="abs chat-box">Lorem Ipsum is simply dummy text of the printing and typesetting industry.</div>
  <div class="abs chat-tab">
    <svg width="310" height="82"><polygon points="0,0 310,0 310,60 155,82 0,60" fill="var(--green)" stroke="#6d8f7c" stroke-width="2"/></svg>
    <span>CHAT WITH US!</span>
  </div>
  <h1 class="abs hero-title heading">Local real estate experts lending to<br>local real estate investors</h1>
  <a class="abs btn btn-green" href="#" style="left:79px;top:802px;width:206px;height:51px">LEARN MORE</a>
  <a class="abs btn btn-green" href="#" style="left:297px;top:802px;width:208px;height:51px">APPLY NOW</a>
</section>

<section class="about">
  <h2 class="abs section-title" style="top:925px"><span class="light">ABOUT </span><span class="strong">US</span></h2>
  <p class="abs about-intro">Lorem Ipsum is simply dummy text of the printing and typesetting industry. Lorem Ipsum has been the industry's standard dummy text ever since the 1500s, when an unknown printer took a galley of type and scrambled it to make a type specimen book.</p>
  <div class="abs feature" style="left:85px">
    <div class="feature-head"><span class="feature-icon"><svg width="40" height="40" fill="none" stroke="#fff" stroke-width="2.5"><circle cx="22" cy="20" r="12"/><circle cx="22" cy="20" r="6"/><circle cx="22" cy="20" r="1.5" fill="#fff"/><path d="M4 20h12M6 15l4 5-4 5"/></svg></span><span class="feature-name">Mission</span></div>
    <p class="feature-text">Lorem Ipsum is simply dummy text of the printing and typesetting industry.</p>
    <a class="read-more" href="#">READ MORE</a>
  </div>
  <div class="abs feature" style="left:439px">
    <div class="feature-head"><span class="feature-icon"><svg width="40" height="40" fill="none" stroke="#fff" stroke-width="2.5"><circle cx="20" cy="20" r="13"/><circle cx="20" cy="20" r="4"/><path d="M20 3v9M20 28v9M3 20h9M28 20h9"/></svg></span><span class="feature-name">Focus</span></div>
    <p class="feature-text">Lorem Ipsum is simply dummy text of the printing and typesetting industry.</p>
    <a class="read-more" href="#">READ MORE</a>
  </div>
  <div class="abs feature" style="left:796px">
    <div class="feature-head"><span class="feature-icon"><svg width="40" height="40" fill="none" stroke="#fff" stroke-width="2.5"><path d="M8 20a12 12 0 0 1 20-9M32 20a12 12 0 0 1-20 9"/><path d="M28 5v6h-6M12 35v-6h6"/><circle cx="16" cy="18" r="2" fill="#fff"/><circle cx="24" cy="22" r="2" fill="#fff"/></svg></span><span class="feature-name">What makes us<br>different</span></div>
    <p class="feature-text">Lorem Ipsum is simply dummy text of the printing and typesetting industry.</p>
    <a class="read-more" href="#">READ MORE</a>
  </div>
</section>

<section class="abs flip">
  <div class="abs flip-photo" role="img" aria-label="Photo of a renovated suburban house with a stone garden wall and lawn"></div>
  <svg class="abs" style="left:0;top:0" width="700" height="420"><polygon points="0,0 656,0 518,420 0,420" fill="var(--green)"/></svg>
</section>
<h2 class="abs flip-title heading">Fix and Flip Loans</h2>
<p class="abs flip-text">Lorem Ipsum is simply dummy text of the printing and typesetting industry. Lorem Ipsum has been the industry's standard dummy text ever since the 1500s, when an unknown printer took a galley of type and scrambled it to make a type specimen book.</p>
<a class="abs btn" href="#" style="left:79px;top:1532px;width:206px;height:51px">LEARN MORE</a>

<section class="abs cta">
  <svg width="1200" height="155"><rect width="1200" height="155" fill="var(--black)"/><polygon points="0,0 720,0 760,77 720,155 0,155" fill="var(--charcoal-2)"/></svg>
</section>
<p class="abs cta-text">Looking for a quality and affordable<br>lender for your <b>next project?</b></p>
<a class="abs cta-link" href="#" style="text-decoration:none">CONTACT US</a>

<section class="abs commercial">
  <div class="abs commercial-photo" role="img" aria-label="Photo of glass office towers against a blue sky"></div>
  <svg class="abs" style="left:0;top:0" width="1200" height="415"><polygon points="535,0 1200,0 1200,415 680,415" fill="var(--green)"/></svg>
</section>
<h2 class="abs commercial-title heading">Commercial Hard Money Loans</h2>
<p class="abs commercial-text">Lorem Ipsum is simply dummy text of the printing and typesetting industry. Lorem Ipsum has been the industry's standard dummy text ever since the 1500s, when an unknown printer took a galley of type and scrambled it to make a type specimen book.</p>
<a class="abs btn" href="#" style="left:914px;top:2096px;width:207px;height:51px">LEARN MORE</a>

<section class="team">
  <h2 class="abs section-title" style="top:2276px"><span class="light">OUR </span><span class="strong">TEAM</span></h2>
  <div class="abs member" style="left:79px;top:2352px"><div class="member-card"></div><div class="member-photo" role="img" aria-label="Portrait photo of team member"></div><h3 class="member-name">Wesley R. Hale</h3><p class="member-bio">Lorem Ipsum is simply dummy text of the printing and typesetting industry. Lorem Ipsum has been the industry's standard dummy text.</p></div>
  <div class="abs member" style="left:623px;top:2352px"><div class="member-card"></div><div class="member-photo" role="img" aria-label="Portrait photo of team member"></div><h3 class="member-name">Anna Brewer</h3><p class="member-bio">Lorem Ipsum is simply dummy text of the printing and typesetting industry. Lorem Ipsum has been the industry's standard dummy text.</p></div>
  <div class="abs member" style="left:79px;top:2634px"><div class="member-card"></div><div class="member-photo" role="img" aria-label="Portrait photo of team member"></div><h3 class="member-name">Wesley R. Hale</h3><p class="member-bio">Lorem Ipsum is simply dummy text of the printing and typesetting industry. Lorem Ipsum has been the industry's standard dummy text.</p></div>
  <div class="abs member" style="left:623px;top:2634px"><div class="member-card"></div><div class="member-photo" role="img" aria-label="Portrait photo of team member"></div><h3 class="member-name">Anna Brewer</h3><p class="member-bio">Lorem Ipsum is simply dummy text of the printing and typesetting industry. Lorem Ipsum has been the industry's standard dummy text.</p></div>
</section>

<footer>
  <div class="abs footer"></div>
  <h3 class="abs footer-title" style="left:99px">TESTIMONIALS</h3>
  <div class="abs quote" style="top:3003px"><span class="avatar" role="img" aria-label="Client portrait photo"></span><p>There are many variations of passages<br>of Lorem Ipsum available..<br><b>-Client Name</b></p></div>
  <div class="abs quote" style="top:3106px"><span class="avatar" role="img" aria-label="Client portrait photo"></span><p>There are many variations of passages<br>of Lorem Ipsum available..<br><b>-Client Name</b></p></div>
  <div class="abs footer-divider"></div>
  <h3 class="abs footer-title" style="left:632px">CONTAT INFO</h3>
  <div class="abs contact-row" style="top:3003px">
    <svg width="80" height="84" fill="none" stroke="#fff" stroke-width="2.5"><polygon points="40,4 74,22 74,62 40,80 6,62 6,22"/><path d="M40 24v38M28 32h24l4 4-4 4H28zM52 46H28l-4 4 4 4h24z"/></svg>
    <p>Lorem Ipsum is simply dummy text of<br>the printing and typesetting industry.</p>
  </div>
  <div class="abs contact-row" style="top:3100px">
    <svg width="80" height="84" fill="none" stroke="#fff" stroke-width="2.5"><polygon points="40,4 74,22 74,62 40,80 6,62 6,22"/><path d="M30 28c-3 3-2 9 4 16s12 10 16 7l2-3-5-5-3 2c-2-1-6-5-7-7l2-3-5-5z"/></svg>
    <p>Phone No. : 123 456 7890<br><br>Email : info@rtvfinance.example</p>
  </div>
  <div class="abs bottom-bar">©RTV Finance - 2016. All Rights Reserved.</div>
</footer>

</body>
</html>
```